KDWB Business Card

Looking for a business card design to incorporate our branding. We want to only use the colors listing in the Branding Package (attached).
Updates

Target Market(s)

People who need their phone or device fixed.

Industry/Entity Type

Electronics

Contact Information for Business Card

Please use:

Brightwick Gadget Clinic LLC
4810 E Harlow Ridge Rd
Suite 417
San Antonio, TX 78163

Marcus Delgrove, Store Manager

(210) 555-0147

Requirements
Must have
• Must include the colors that are contained within the Branding Package PDF file.

```html
<!DOCTYPE html>
<html lang="en">
<head>
<meta charset="utf-8">
<title>Brightwick Gadget Clinic – Business Card</title>
<link rel="stylesheet" href="https://fonts.googleapis.com/css2?family=Roboto:wght@300;400&display=swap">
<style>
  :root {
    --page-bg: #e9e6e1;
    --card-white: #f4f4f5;
    --card-dark: #1c1c1e;
    --brand-orange: #e35a26;
    --brand-lime: #c4cf3a;
    --text-light: #e9e9ea;
    --text-dark: #3a3a3c;
  }
  * { box-sizing: border-box; margin: 0; padding: 0; }
  html, body { width: 1200px; height: 902px; overflow: hidden; }
  body {
    background: var(--page-bg);
    font-family: "Roboto", Arial, sans-serif;
    font-weight: 300;
    position: relative;
  }
  .card {
    position: absolute;
    top: 296px;
    width: 540px;
    height: 309px;
    border-radius: 4px;
    overflow: hidden;
    box-shadow: 0 10px 30px rgba(0,0,0,0.18);
  }
  .card--front { left: 40px; background: var(--card-white); }
  .card--back { left: 620px; background: var(--card-dark); }

  .card__photo {
    position: absolute;
    inset: 0;
  }
  .card--front .card__photo {
    background: radial-gradient(ellipse at 40% 45%, rgba(200,190,180,0.35), rgba(244,244,245,0) 60%);
  }
  .card--back .card__photo {
    background:
      radial-gradient(ellipse 120px 150px at 68% 48%, rgba(70,90,95,0.45), rgba(28,28,30,0) 100%),
      linear-gradient(135deg, #242426 0%, #1a1a1c 60%, #202022 100%);
  }

  .brand {
    position: absolute;
    display: flex;
    align-items: center;
    gap: 12px;
  }
  .brand__mark {
    width: 34px;
    height: 34px;
    background: var(--brand-orange);
  }
  .brand__name {
    color: var(--brand-orange);
    font-weight: 300;
    font-size: 27px;
    letter-spacing: 0.3px;
    white-space: nowrap;
  }
  .card--front .brand { left: 56px; top: 134px; }
  .card--back .brand { left: 100px; top: 70px; }
  .card--back .brand__name { font-size: 24px; }

  .contact {
    position: absolute;
    right: 60px;
    top: 140px;
    text-align: right;
    color: var(--text-light);
  }
  .contact__name { font-size: 21px; }
  .contact__role { font-size: 13px; color: var(--brand-orange); margin-top: 2px; }
  .contact__phone { font-size: 15px; margin-top: 18px; }
  .contact__web { font-size: 13px; margin-top: 18px; line-height: 1.5; }
</style>
</head>
<body>
  <section class="card card--front" aria-label="Card front">
    <div class="card__photo" role="img" aria-label="Faint photo of a hand holding a smartphone"></div>
    <div class="brand">
      <span class="brand__mark"></span>
      <span class="brand__name">Brightwick Gadget Clinic</span>
    </div>
  </section>

  <section class="card card--back" aria-label="Card back">
    <div class="card__photo" role="img" aria-label="Dark world map with a smartphone photo overlaid"></div>
    <div class="brand">
      <span class="brand__mark"></span>
      <span class="brand__name">Brightwick Gadget Clinic</span>
    </div>
    <div class="contact">
      <p class="contact__name">Marcus Delgrove</p>
      <p class="contact__role">Store Manager</p>
      <p class="contact__phone">(210) 555-0147</p>
      <p class="contact__web">marcus@brightwickclinic.com<br>www.brightwickclinic.com</p>
    </div>
  </section>
</body>
</html>
```